Elevating our current Business Card Design

We want to elevate our current business card with a new design to look like a zenith 300 company. We are a premium lubricant distributor (oil and grease).
We need 2 versions, version 1 is as per the uploaded a copy of our current business card with the English version.
For our Chinese version we need to use the front to be English in English and have the back of the card designed exactly like the front for all info to be in Chinese.
The design template needs to be such that we can amend the template with adding different information for each person's card.
The background colour of the card can be changed- we just need to clearly see all information on the card and logos.
The QJR and Ember steady logos cannot have any colour or display changes- only use the logos attached.
All logos need to be included and all information from the attached current card

```html
<!DOCTYPE html>
<html lang="en">
<head>
<meta charset="utf-8">
<title>Kestrel Business Card</title>
<link href="https://fonts.googleapis.com/css2?family=Exo+2:wght@600&family=Open+Sans:wght@400;600;700&display=swap" rel="stylesheet">
<style>
  :root {
    --stage: #242424;
    --card: #1e1e22;
    --red: #ec2a27;
    --white: #f4f4f4;
    --grey: #9a9a9a;
    --warm: #3a342e;
  }
  * { box-sizing: border-box; margin: 0; padding: 0; }
  html, body { width: 1200px; height: 780px; overflow: hidden; background: var(--stage); }
  body { font-family: "Open Sans", sans-serif; color: var(--white); position: relative; }

  .card {
    position: absolute;
    width: 540px; height: 310px;
    background: var(--card);
    border-bottom: 6px solid var(--red);
    box-shadow: 0 18px 40px rgba(0,0,0,.55);
    overflow: hidden;
  }
  .card--front { left: 40px; top: 60px; }
  .card--back { left: 620px; top: 410px; }

  /* front */
  .brand-mark {
    position: absolute; left: 0; right: 0; top: 70px;
    display: flex; align-items: center; justify-content: center; gap: 18px;
  }
  .brand-mark__dot { width: 40px; height: 40px; border-radius: 50%; background: var(--red); }
  .brand-mark__name { font-weight: 700; font-size: 64px; color: var(--red); letter-spacing: 2px; }

  .accreditations {
    position: absolute; left: 24px; right: 24px; bottom: 22px;
    display: flex; align-items: center; gap: 12px;
  }
  .network-name { font-weight: 700; font-size: 13px; color: var(--white); line-height: 1.1; }
  .network-name small { display: block; font-size: 7px; font-weight: 600; letter-spacing: 1px; }
  .cert-badge { width: 34px; height: 34px; border-radius: 50%; background: #f07a22; border: 3px solid var(--grey); flex: none; }
  .partner-strip {
    display: flex; align-items: center; justify-content: space-between;
    border: 2px solid var(--red); border-radius: 4px;
    padding: 6px 10px; flex: 1;
  }
  .partner-strip__name { font-weight: 700; font-size: 11px; color: var(--red); line-height: 1.2; }

  /* back */
  .backdrop-dots {
    position: absolute; right: -40px; top: -30px; width: 300px; height: 320px;
    background: radial-gradient(ellipse at 60% 45%, var(--warm) 0%, rgba(58,52,46,.5) 40%, transparent 70%);
    opacity: .7;
  }
  .holder { position: absolute; left: 40px; top: 150px; }
  .holder__name { font-family: "Exo 2", sans-serif; font-weight: 600; font-size: 32px; color: var(--red); line-height: 1; }
  .holder__role { font-size: 14px; color: var(--white); margin-top: 6px; }
  .divider { position: absolute; left: 272px; top: 60px; width: 2px; height: 140px; background: var(--white); }
  .contacts { position: absolute; left: 292px; top: 62px; list-style: none; }
  .contacts li { display: flex; align-items: center; gap: 10px; font-size: 12.5px; height: 27px; }
  .contacts svg { width: 15px; height: 15px; flex: none; }
  .address { position: absolute; left: 0; right: 0; bottom: 24px; text-align: center; font-size: 13px; }
</style>
</head>
<body>

<section class="card card--front" aria-label="Card front">
  <div class="brand-mark">
    <span class="brand-mark__dot"></span>
    <span class="brand-mark__name">KESTREL</span>
  </div>
  <div class="accreditations">
    <p class="network-name">Ember steady<small>NETWORK MEMBER</small></p>
    <span class="cert-badge"></span>
    <div class="partner-strip">
      <span class="partner-strip__name">KESTREL<br>LUBRICANT CO.</span>
      <span class="partner-strip__name">NORVALE<br>PREMIUM LUBRICANTS</span>
    </div>
    <span class="cert-badge"></span>
    <span class="cert-badge"></span>
  </div>
</section>

<section class="card card--back" aria-label="Card back">
  <div class="backdrop-dots" role="img" aria-label="Faint warm decorative area behind contact details"></div>
  <div class="holder">
    <p class="holder__name">Dana Morrow</p>
    <p class="holder__role">Administration Executive</p>
  </div>
  <div class="divider"></div>
  <ul class="contacts">
    <li><svg viewBox="0 0 24 24" fill="none" stroke="#ec2a27" stroke-width="2.2"><path d="M5 4h4l2 5-2.5 1.5a11 11 0 0 0 5 5L15 13l5 2v4a2 2 0 0 1-2 2A16 16 0 0 1 3 6a2 2 0 0 1 2-2z"/></svg>1300 642 117</li>
    <li><svg viewBox="0 0 24 24" fill="none" stroke="#f4f4f4" stroke-width="2"><rect x="6" y="2" width="12" height="20" rx="2"/><line x1="11" y1="18" x2="13" y2="18"/></svg>+61 400 218 765</li>
    <li><svg viewBox="0 0 24 24" fill="#ec2a27"><rect x="3" y="9" width="18" height="12" rx="2"/><rect x="7" y="3" width="10" height="7" fill="none" stroke="#ec2a27" stroke-width="2"/></svg>+61 8 9000 4521</li>
    <li><svg viewBox="0 0 24 24" fill="none" stroke="#ec2a27" stroke-width="2"><circle cx="12" cy="12" r="9"/><path d="M3 12h18M12 3a14 14 0 0 1 0 18M12 3a14 14 0 0 0 0 18"/></svg>www.kestreldirect.com</li>
    <li><svg viewBox="0 0 24 24" fill="none" stroke="#ec2a27" stroke-width="2"><rect x="3" y="5" width="18" height="14" rx="1"/><path d="M3 6l9 7 9-7"/></svg>dana.morrow@kestreldirect.com</li>
  </ul>
  <p class="address">14 Harbour Link Drive Westvale, WA 6999</p>
</section>

</body>
</html>
```